Psychotherapy, Life Coaching, Writer, Motivational Speaker

I am a psychotherapist, life coach, writer and speaker on health and wellness issues. I am a humanist - who believes that we are born to self-actualize - but life - changes that course. That we develop armor and coping mechanisms that divert our growth. I help people examine their road blocks to happiness. My business is unique in that I do concierge therapy. I work intensively - with multi-day sessions, I work internationally through tele-therapy - and traditionally - in an office space. My work is tailored to your needs.

Target Market(s)

Broad

Industry/Entity Type

Health

Contact Information for Business Card

Listen And Grow
Sam Perriton
248 East 39th Street
New York, NY 10027
(305) 555-0173

Requirements
Must have
• Clean lines... not too busy...
• FB page listing: Listen And Grow
• my Web page: www.listenandgrow-example.com
Nice to have
• I would love to be able to list the services: Psychotherapist, Life Coach, Motivational Speaker and Writer - but also don't want a crazy crowded card. Feel free to use the back for description.
Should not have
• Stay away from corny imagery - lotus flowers, zen, lily pond, clouds.

```html
<!DOCTYPE html>
<html lang="en">
<head>
<meta charset="utf-8">
<title>Listen And Grow – Business Card</title>
<link rel="stylesheet" href="https://fonts.googleapis.com/css2?family=Lato:wght@400;700&display=swap">
<style>
  :root {
    --bg: #e6e6e6;
    --paper: #ffffff;
    --ink: #111111;
    --brand-blue: #4a78b5;
    --band-blue: #4d7dba;
    --night: #000000;
    --on-dark: #ffffff;
  }
  * { box-sizing: border-box; margin: 0; padding: 0; }
  html, body {
    width: 1200px; height: 720px; overflow: hidden;
    background: var(--bg);
    font-family: "Lato", Arial, sans-serif;
  }
  .card {
    position: absolute; top: 241px;
    width: 420px; height: 240px;
    border-radius: 12px; overflow: hidden;
    background: var(--paper);
  }
  .card--front { left: 148px; }
  .card--back { left: 633px; }

  .front__wave { position: absolute; inset: 0; }
  .front__brand {
    position: absolute; left: 15px; top: 16px;
    font-size: 23px; font-weight: 700; color: var(--brand-blue);
  }
  .front__address {
    position: absolute; right: 12px; top: 17px;
    font-size: 12px; line-height: 15px; text-align: right; color: var(--ink);
  }
  .front__person { position: absolute; left: 20px; top: 119px; color: var(--on-dark); }
  .person__name { font-size: 13px; }
  .person__name strong { font-size: 16px; color: var(--brand-blue); }
  .person__role { font-size: 12.5px; margin-top: 2px; }
  .contact { position: absolute; left: 20px; top: 163px; list-style: none; color: var(--on-dark); font-size: 13px; line-height: 16px; }
  .contact li { display: flex; align-items: center; gap: 4px; }
  .contact svg { width: 11px; height: 11px; flex: none; }
  .contact .square { width: 10px; height: 10px; background: var(--brand-blue); border-radius: 1px; margin-right: 1px; }

  .back__brand {
    position: absolute; top: 58px; left: 0; right: 0; text-align: center;
    font-size: 20px; font-weight: 700; color: var(--brand-blue);
  }
  .back__appointment {
    position: absolute; top: 134px; left: 0; right: 0; text-align: center;
    font-size: 13px; color: var(--ink);
  }
  .back__services {
    position: absolute; left: 0; right: 0; bottom: 0; height: 32px;
    background: var(--band-blue); color: var(--on-dark);
    font-size: 13px; text-align: center; line-height: 32px;
  }
</style>
</head>
<body>
  <section class="card card--front">
    <svg class="front__wave" viewBox="0 0 420 240" aria-hidden="true">
      <path d="M0,58 C170,54 330,110 420,240 L0,240 Z" fill="var(--brand-blue)"/>
      <path d="M0,92 C170,90 335,150 414,240 L0,240 Z" fill="var(--night)"/>
    </svg>
    <h1 class="front__brand">Listen And Grow</h1>
    <p class="front__address">248 East 39th Street<br>New York, NY 10027</p>
    <div class="front__person">
      <p class="person__name"><strong>Sam Perriton,</strong> LMHC, NCC</p>
      <p class="person__role">Psychotherapist.</p>
    </div>
    <ul class="contact">
      <li><svg viewBox="0 0 12 12"><path d="M1 4 Q6 0 11 4 L9 6 L8 4.5 L4 4.5 L3 6 Z M3 6 L9 6 L10 10 L2 10 Z" fill="var(--brand-blue)"/></svg>(305) 555-0173</li>
      <li><svg viewBox="0 0 12 12"><rect x="1" y="2.5" width="10" height="7" fill="var(--brand-blue)"/><path d="M1 2.5 L6 6.5 L11 2.5" stroke="var(--night)" fill="none" stroke-width="1"/></svg>sperriton.office@example.com</li>
      <li><svg viewBox="0 0 12 12"><g fill="none" stroke="var(--brand-blue)" stroke-width="1"><circle cx="6" cy="6" r="5"/><ellipse cx="6" cy="6" rx="2.2" ry="5"/><path d="M1 6 H11 M2 3.5 H10 M2 8.5 H10"/></g></svg>www.listenandgrow-example.com</li>
      <li><span class="square"></span>Listen And Grow</li>
    </ul>
  </section>

  <section class="card card--back">
    <h2 class="back__brand">Listen and Grow</h2>
    <p class="back__appointment">Your Next Appoinment is at...................... at.............. am/pm</p>
    <p class="back__services">Psychotherapy, Coaching, Wellness Media</p>
  </section>
</body>
</html>
```